Business Card for Multi-Brand Sportswear Company

We are looking for a business card which represents our company and the multiple brands within it.

The company: Fen Athletics (LTD)
The brands: Fen, TavaPuni, ElmStretch, Grit and Rain

Employees using these cards would be representing Fen Athletics, rather than any of the individual brands. You will see a current design within the uploaded files, to give some inspiration. The actual text of the brands is not necessary, but the logos should be on there is some format.

Our creative minds on this are stretched, so we are looking for someone to make this their own, and show us what a good business card should look like.

We may like to get these printed with spot gloss, so keep that in mind with your designs.

www.fenathletics.co.uk

Industry/Entity Type

Business

Contact Information for Business Card

Leo Pemberton-Hale
Operations Manager
(+44) 1632 960 418
Leo@fenathletics.co.uk
www.fenathletics.co.uk

Font styles to use
Sans Serif
Other font styles liked:
• Eurostile

Colors
ffffff

Requirements
Nice to have
• Dark (black) background

```html
<!DOCTYPE html>
<html lang="en">
<head>
<meta charset="utf-8">
<title>Fen Athletics – Business Card</title>
<link href="https://fonts.googleapis.com/css2?family=Open+Sans:wght@400;600;700&display=swap" rel="stylesheet">
<style>
  :root{
    --backdrop:#c9c9c9;
    --card-white:#ffffff;
    --card-black:#1c1c1c;
    --ink:#1a1a1a;
    --accent:#e3141b;
    --rule:#f2a7aa;
    --muted:#6d6d6d;
    --light:#e9e9e9;
  }
  *{box-sizing:border-box;margin:0;padding:0}
  html,body{width:1200px;height:900px;overflow:hidden}
  body{background:var(--backdrop);font-family:"Open Sans",Arial,sans-serif;position:relative}
  .card{position:absolute;top:306px;width:440px;height:271px;border-radius:10px;overflow:hidden}
  .card--front{left:149px;background:var(--card-white);color:var(--ink)}
  .card--back{left:608px;background:var(--card-black)}

  .wordmark{position:absolute;text-align:right}
  .wordmark__name{font-weight:700;letter-spacing:.5px;line-height:1}
  .wordmark__tag{font-size:7px;letter-spacing:1.2px;font-weight:400;margin-top:3px}
  .card--front .wordmark{right:27px;top:64px}
  .card--front .wordmark__name{font-size:24px;color:var(--ink)}
  .card--front .wordmark__tag{color:var(--ink)}

  .holder{position:absolute;left:28px;top:120px}
  .holder__name{color:var(--accent);font-weight:700;font-size:14.5px;line-height:1.2}
  .holder__role{font-size:12px;line-height:1.3}
  .divider{position:absolute;left:28px;right:27px;top:169px;height:1.5px;background:var(--rule)}

  .address{position:absolute;left:28px;top:200px;font-size:12px;line-height:1.45}
  .contacts{position:absolute;right:27px;top:193px;list-style:none;font-size:12px;line-height:16px;text-align:right}
  .contacts li{display:flex;justify-content:flex-end;align-items:center;gap:6px}
  .contacts svg{width:9px;height:9px;flex:none}

  .pattern{position:absolute;inset:0;background:linear-gradient(135deg,#222 0%,#171717 100%)}
  .card--back .wordmark{left:0;right:0;top:126px;text-align:center}
  .card--back .wordmark__name{font-size:32px;color:#fff}
  .card--back .wordmark__tag{color:#fff;font-size:8px}

  .brands{position:absolute;left:56px;right:56px;top:204px;display:flex;justify-content:space-between;align-items:center}
  .brand{font-weight:700;font-size:13px;color:var(--light);display:flex;align-items:center;gap:6px}
  .brand__dot{width:12px;height:12px;border-radius:50%;background:var(--accent)}
</style>
</head>
<body>
  <section class="card card--front">
    <div class="wordmark">
      <div class="wordmark__name">FEN ATHLETICS</div>
      <div class="wordmark__tag">PERFORMANCE WEAR</div>
    </div>
    <div class="holder">
      <p class="holder__name">Tom Ashcroft</p>
      <p class="holder__role">Managing Director</p>
    </div>
    <div class="divider"></div>
    <p class="address">Low Fields, Marsh End,<br>Ely, CB7 2QX</p>
    <ul class="contacts">
      <li>+44(0)1632 960418
        <svg viewBox="0 0 10 10"><path fill="#e3141b" d="M1 4c0-2 2-3 4-3s4 1 4 3H7V3H3v1zM2 5h6l1 4H1z"/></svg></li>
      <li>tom@fenathletics.co.uk
        <svg viewBox="0 0 10 10"><rect x="1" y="2" width="8" height="6" fill="#e3141b"/><path d="M1 2l4 3 4-3" stroke="#fff" fill="none"/></svg></li>
      <li>www.fenathletics.co.uk
        <svg viewBox="0 0 10 10"><circle cx="5" cy="5" r="4.5" fill="#e3141b"/><path d="M1 5h8M5 .5v9" stroke="#fff" stroke-width=".8"/></svg></li>
    </ul>
  </section>

  <section class="card card--back">
    <div class="pattern" role="img" aria-label="Faint repeated brand-name pattern on black"></div>
    <div class="wordmark">
      <div class="wordmark__name">FEN ATHLETICS</div>
      <div class="wordmark__tag">PERFORMANCE WEAR</div>
    </div>
    <div class="brands">
      <span class="brand">TavaPuni</span>
      <span class="brand"><span class="brand__dot"></span>Grit and Rain</span>
      <span class="brand">Fen</span>
      <span class="brand">ElmStretch</span>
    </div>
  </section>
</body>
</html>
```